TalkHarbor - Language Coaching Services

Sleek, innovative, trendy design for Language Coaching business.

TalkHarbor is a new UK based company that provides Language Coaching services. We offer highly personalized on-line and face to face language courses. We also impart learning techniques workshops based on the latest neuroscience research for second-language acquisition.

Target Market(s)

See attached info

Industry/Entity Type

Consulting

Contact Information for Business Card

TalkHarbor
DaniaKV@talkharbor.co.uk
TalkHarbor.co.uk
London, UK

Font styles to use
Sans Serif

```html
<!DOCTYPE html>
<html lang="en">
<head>
<meta charset="utf-8">
<title>TalkHarbor Business Card</title>
<link href="https://fonts.googleapis.com/css2?family=Lato:wght@300;400;700&family=Montserrat:wght@400;600&display=swap" rel="stylesheet">
<style>
  :root {
    --backdrop: #2f2f2f;
    --card-white: #ffffff;
    --brand-blue: #0a8fcf;
    --brand-blue-light: #03a9e4;
    --brand-blue-deep: #0a78b5;
    --ink: #1d1d1d;
    --ink-soft: #444444;
    --rule: #9a9ab0;
  }
  * { margin: 0; padding: 0; box-sizing: border-box; }
  html, body { width: 1200px; height: 1200px; overflow: hidden; }
  body { background: var(--backdrop); position: relative; font-family: "Lato", sans-serif; }

  .card { position: absolute; top: 310px; width: 365px; height: 594px; }
  .card--front { left: 234px; background: var(--card-white); text-align: center; }
  .card--back {
    left: 628px; width: 368px;
    background: linear-gradient(160deg, var(--brand-blue-light) 0%, #079bd6 45%, var(--brand-blue-deep) 100%);
  }

  .brand-mark { position: absolute; left: 124px; top: 89px; width: 116px; height: 116px; border: 7px solid var(--brand-blue); border-radius: 50%; }
  .brand-name {
    position: absolute; left: 0; right: 0; top: 208px;
    font-family: "Montserrat", sans-serif; font-weight: 600; font-size: 41px;
    letter-spacing: 1px; color: var(--brand-blue);
  }

  .person { position: absolute; left: 0; right: 0; top: 338px; }
  .person__name { font-family: "Montserrat", sans-serif; font-size: 21px; font-weight: 600; color: var(--brand-blue); }
  .person__name .surname { font-weight: 400; }
  .person__role { font-size: 16px; color: var(--ink-soft); margin-top: 0; }

  .divider { position: absolute; left: 87px; width: 190px; display: flex; align-items: center; justify-content: center; gap: 3px; }
  .divider::before, .divider::after { content: ""; flex: 1; height: 1.5px; background: var(--rule); }
  .divider--contact { top: 395px; }
  .divider--location { top: 508px; left: 88px; width: 195px; }
  .divider .icons { display: flex; gap: 3px; margin: 0 2px; }

  .contact { position: absolute; left: 0; right: 0; top: 431px; font-size: 17px; line-height: 22px; color: var(--ink); }
  .location { position: absolute; left: 0; right: 0; top: 535px; font-size: 17px; color: var(--ink); }

  .back-mark { position: absolute; left: 56px; top: 170px; width: 256px; height: 256px; border: 16px solid var(--card-white); border-radius: 50%; display: flex; align-items: center; justify-content: center; }
  .back-mark__name { font-family: "Montserrat", sans-serif; font-weight: 600; font-size: 28px; color: var(--card-white); }
  .back-url { position: absolute; left: 0; right: 0; top: 523px; text-align: center; font-size: 17px; color: var(--card-white); }
</style>
</head>
<body>
  <section class="card card--front">
    <div class="brand-mark"></div>
    <div class="brand-name">TALKHARBOR</div>

    <div class="person">
      <div class="person__name">MARCUS <span class="surname">HALE</span></div>
      <div class="person__role">Managing Director</div>
    </div>

    <div class="divider divider--contact">
      <div class="icons">
        <svg width="24" height="24" viewBox="0 0 24 24" aria-label="phone"><circle cx="12" cy="12" r="12" fill="#0a8fcf"/><path d="M7 10 q5-4 10 0 l-1.5 1.5 -2-1 v-1 h-3 v1 l-2 1z M8 12 h8 v4 h-8z" fill="#fff"/></svg>
        <svg width="24" height="24" viewBox="0 0 24 24" aria-label="email"><circle cx="12" cy="12" r="12" fill="#0a8fcf"/><rect x="6.5" y="8" width="11" height="8" fill="#fff"/><path d="M6.5 8 l5.5 4.5 5.5-4.5" fill="none" stroke="#0a8fcf" stroke-width="1.2"/></svg>
        <svg width="24" height="24" viewBox="0 0 24 24" aria-label="website"><circle cx="12" cy="12" r="12" fill="#0a8fcf"/><circle cx="12" cy="12" r="6" fill="#fff"/><path d="M9 9 q2 1 1 3 q2 1 1 3 M14 8 q-1 2 1 3" fill="none" stroke="#0a8fcf" stroke-width="1.3"/></svg>
      </div>
    </div>

    <div class="contact">
      044 777 1234<br>
      DaniaKV@talkharbor.co.uk<br>
      www.TalkHarbor.co.uk
    </div>

    <div class="divider divider--location">
      <div class="icons">
        <svg width="24" height="24" viewBox="0 0 24 24" aria-label="location"><circle cx="12" cy="12" r="12" fill="#0a8fcf"/><path d="M12 18.5 c-3-4-4.5-6-4.5-8.2 a4.5 4.5 0 0 1 9 0 c0 2.2-1.5 4.2-4.5 8.2z" fill="#fff"/><circle cx="12" cy="10.3" r="1.8" fill="#0a8fcf"/></svg>
      </div>
    </div>
    <div class="location">London, UK</div>
  </section>

  <section class="card card--back">
    <div class="back-mark"><span class="back-mark__name">TalkHarbor</span></div>
    <div class="back-url">www.TalkHarbor.co.uk</div>
  </section>
</body>
</html>
```